Norvane Freight and Provision Service Brochure

Please see http://www.norvanefreight.example for who we are and what we do.
We would like to see a design that matches the industry we work in i.e. Oil and Gas. The design should communicate large, heavy field operations, supply of vast bulk fuel quantities to our US and Afghan Military customers, plus financial independence and the companies whatever it takes attitude operation in remote often hostile areas. Dark colors like on the website - contrasting our green logo. A strong focus on our past performance/past experience.

Target Market(s)

Military Customers, Partners, Subcontractors

Industry/Entity Type

Industry

Contact Information for Business Card

Display of Address, Phone, email etc. of our 4 offices

Font styles to use
Sans Serif

Requirements
Must have
• Glossy brochure, modern, cool design. Great display (map) of our offices in the Middle East, Europe and Central Asia. A focus on our past performance/past experience. Customer logos/references
Nice to have
• Prominent highlighted watermark logo
Should not have
• Standard A4/Letter brochure

```html
<!DOCTYPE html>
<html lang="en">
<head>
<meta charset="utf-8">
<title>Norvane Freight and Provision – Where We Work</title>
<link rel="stylesheet" href="https://fonts.googleapis.com/css2?family=Barlow:wght@400;500;600&family=Michroma&family=Arimo&display=swap">
<style>
  :root {
    --navy: #0b1a5c;
    --lime: #8cf000;
    --panel-grey: rgba(205, 206, 210, 0.9);
    --text-dark: #222;
    --white: #fff;
    --map-grey: #a7adad;
  }
  * { margin: 0; padding: 0; box-sizing: border-box; }
  html, body { width: 1200px; height: 999px; overflow: hidden; background: var(--white); }
  body { position: relative; font-family: "Barlow", sans-serif; }

  .page { position: absolute; top: 287px; width: 600px; height: 425px; overflow: hidden; }
  .page--left { left: 0; }
  .page--right { left: 600px; width: 600px; }

  .photo-handshake {
    position: absolute; inset: 0;
    background: linear-gradient(180deg, #b9d2ea 0%, #6f93bf 30%, #2e4c7c 60%, #3a4f70 100%);
  }
  .title-band {
    position: absolute; left: 0; top: 123px; width: 414px; height: 55px;
    background: var(--navy);
  }
  .title-band h1 {
    position: absolute; left: 60px; top: 20px;
    font-family: "Michroma", sans-serif; font-weight: 400;
    font-size: 13px; letter-spacing: 0.3px; color: var(--white);
  }
  .network-panel {
    position: absolute; left: 414px; top: 123px; width: 186px; height: 302px;
    background: var(--panel-grey);
  }
  .network-panel h2 {
    position: absolute; left: 33px; top: 62px;
    font-size: 10px; font-weight: 600; color: var(--navy);
  }
  .network-panel p {
    position: absolute; left: 33px; top: 77px; width: 118px;
    font-size: 7.6px; line-height: 9.7px; color: var(--text-dark);
  }
  .folio {
    position: absolute; top: 394px; width: 20px; height: 31px;
    background: var(--lime); color: var(--white);
    font-size: 6px; text-align: center; line-height: 31px;
  }
  .page--left .folio { left: 538px; }
  .page--right .folio { left: 538px; }

  .band-lime { position: absolute; left: 0; top: 0; width: 600px; height: 218px; background: var(--lime); }
  .band-navy { position: absolute; left: 0; top: 218px; width: 600px; height: 207px; background: var(--navy); }

  .region h3 { font-size: 9.5px; font-weight: 500; }
  .region p { font-size: 7.4px; line-height: 9.3px; margin-top: 3px; }
  .region--asia { position: absolute; left: 40px; top: 46px; width: 240px; }
  .region--asia h3 { color: var(--navy); font-weight: 600; }
  .region--asia p { color: var(--white); }
  .region--europe { position: absolute; left: 316px; top: 239px; width: 242px; }
  .region--europe h3 { color: var(--lime); }
  .region--europe p { color: var(--white); }

  .map-frame { position: absolute; width: 257px; height: 150px; border: 5px solid; }
  .map-frame--asia { left: 301px; top: 45px; border-color: var(--navy); }
  .map-frame--europe { left: 40px; top: 238px; border-color: var(--lime); }
  .map-fill { width: 100%; height: 100%; }
  .map-fill--asia { background: linear-gradient(135deg, #b3b9b9, #8f9595 60%, #a9afaf); }
  .map-fill--europe { background: linear-gradient(135deg, #f2f2f2 0%, #b9bebe 40%, #a2a8a8 100%); }
  .pointer { position: absolute; }

  .page-label {
    position: absolute; top: 773px; width: 200px; text-align: center;
    font-family: "Arimo", sans-serif; font-size: 24px; color: #111;
  }
</style>
</head>
<body>
  <section class="page page--left">
    <div class="photo-handshake" role="img" aria-label="Business handshake in front of glass office towers under a blue sky"></div>
    <div class="title-band"><h1>WHERE WE WORK</h1></div>
    <div class="network-panel">
      <h2>Our Network</h2>
      <p>Without solid local relationships, efficiencies, western technology and state of the art processes mean little. It is essential to have partners with a vast, genuine sphere of influence in their regions. Our excellent network of trustworthy, in-regions partners and relationships with highly placed contacts within the local government administration of the countries we operate in will prove valuable to timely and complete mission accomplishment.</p>
    </div>
    <div class="folio">8</div>
  </section>

  <section class="page page--right">
    <div class="band-lime"></div>
    <div class="band-navy"></div>

    <article class="region region--asia">
      <h3>Afghanistan &amp; Central Asia</h3>
      <p>For a decade we provide critical, life-sustaining transportation and supply services that empower military and peace keeping forces to accomplish missions in challenging and austere environments in Afghanistan and Central Asia. Norvane is our customer's solid link in a fragile supply chain of Petroleum Products throughout Central Asia. Today Norvane is the largest supplier of fuel volumes to international organisations in Afghanistan. With a complex transportation network Norvane has demonstrated its' capability of operating in a volatile environments with poor road networks. 31,000 full container loads/truck loads of dry cargo delivered on time and 350,000 MT of Petroleum Products sourced, transported and distributed in the last 36 months within the demanding confines of government contract and associated performance metrics speaks for itself.</p>
    </article>
    <svg class="pointer" style="left:293px;top:111px" width="8" height="14" viewBox="0 0 8 14"><polygon points="8,0 0,7 8,14" fill="var(--navy)"/></svg>
    <div class="map-frame map-frame--asia">
      <div class="map-fill map-fill--asia" role="img" aria-label="Map of Central Asia with pins marking Afghanistan and nearby office locations"></div>
    </div>

    <div class="map-frame map-frame--europe">
      <div class="map-fill map-fill--europe" role="img" aria-label="Map of Europe with a pin marking the Amsterdam office"></div>
    </div>
    <svg class="pointer" style="left:297px;top:306px" width="8" height="14" viewBox="0 0 8 14"><polygon points="0,0 8,7 0,14" fill="var(--lime)"/></svg>
    <article class="region region--europe">
      <h3>Middle East/Central &amp; Eastern Europe/Eastern Africa</h3>
      <p>Drawing on our experience and demonstrated total solutions capabilities as well as our capabilities to overcome obstacles in austere environments empowered the company to deliver integrated fuel supply chain solutions to commercial sector and military customers from as far as Bulgaria to Somalia or the United Arab Emirates. Today Norvane manages total logistics solutions to both US Government agencies and the commercial market from its offices in Amsterdam, Dubai, Riga and Limassol. We source and supply petroleum products to countries in Central &amp; Eastern Europe the Middle East and the Eastern Africa.</p>
    </article>
    <div class="folio">9</div>
  </section>

  <div class="page-label" style="left:183px">Page 8</div>
  <div class="page-label" style="left:804px">Page 9</div>
</body>
</html>
```